Business Cards - New Logo Rebranding

Hello We know have a red and blue logo and are looking to create new cards. We are looking for the best creativity of the new logo merged with some of the existing artwork provided.

Target Market(s)

Realtors

Industry/Entity Type

Real Estate

Contact Information for Business Card

New logo with rebranded colors

Requirements
Must have
• Creative use of the new logo

```html
<!DOCTYPE html>
<html lang="en">
<head>
<meta charset="utf-8">
<title>Summit Crest Business Cards</title>
<link href="https://fonts.googleapis.com/css2?family=Arimo:wght@400;700&display=swap" rel="stylesheet">
<style>
  :root {
    --blue: #0a6fbd;
    --red: #e0323c;
    --white: #ffffff;
    --ground: #2e2e2e;
    --ink-blue: #0a5ea8;
  }
  * { margin: 0; padding: 0; box-sizing: border-box; }
  html, body { width: 1200px; height: 689px; overflow: hidden; }
  body {
    background: var(--ground);
    font-family: "Arimo", Arial, sans-serif;
    position: relative;
  }
  .card {
    position: absolute;
    top: 200px;
    width: 500px;
    height: 286px;
    border-radius: 16px;
    overflow: hidden;
  }
  .card-back { left: 60px; background: var(--blue); color: var(--white); }
  .card-front { left: 640px; background: var(--white); display: flex; }

  .brand {
    position: absolute;
    display: flex;
    flex-direction: column;
    align-items: center;
  }
  .brand-mark {
    width: 70px; height: 70px;
    border-radius: 50%;
    border: 4px solid currentColor;
    margin-bottom: 12px;
  }
  .brand-name {
    font-weight: 700;
    font-size: 30px;
    letter-spacing: 1px;
    text-transform: uppercase;
  }
  .brand-tagline {
    font-size: 9px;
    letter-spacing: 1.2px;
    text-transform: uppercase;
    margin-top: 4px;
  }
  .card-back .brand { left: 0; right: 0; top: 46px; }
  .services {
    position: absolute;
    left: 0; right: 0; bottom: 34px;
    text-align: center;
    font-size: 13px;
    letter-spacing: 0.6px;
  }

  .front-logo-panel {
    position: relative;
    width: 232px;
    height: 100%;
    color: var(--ink-blue);
    border-right: 4px solid var(--red);
  }
  .front-logo-panel .brand { left: 0; right: 0; top: 78px; }
  .front-logo-panel .brand-mark { border-color: var(--red); width: 62px; height: 62px; }
  .front-logo-panel .brand-name { font-size: 24px; }
  .front-logo-panel .brand-tagline { font-size: 7.5px; }

  .contact-panel {
    flex: 1;
    background: var(--blue);
    color: var(--white);
    padding: 70px 0 0 28px;
  }
  .person-name { font-size: 21px; font-weight: 700; }
  .person-title { font-size: 11px; margin-top: 3px; }
  .contact-list { list-style: none; margin-top: 34px; }
  .contact-list li {
    display: flex;
    align-items: center;
    font-size: 11.5px;
    line-height: 1;
    margin-bottom: 8px;
  }
  .contact-list svg { width: 11px; height: 11px; margin-right: 8px; flex: none; }
</style>
</head>
<body>

<section class="card card-back">
  <div class="brand">
    <div class="brand-mark"></div>
    <div class="brand-name">Summit Crest</div>
    <div class="brand-tagline">Inspection Professionals</div>
  </div>
  <p class="services">HOME • SEWER • MOLD • COMMERCIAL • TERMITE • ROOF</p>
</section>

<section class="card card-front">
  <div class="front-logo-panel">
    <div class="brand">
      <div class="brand-mark"></div>
      <div class="brand-name">Summit Crest</div>
      <div class="brand-tagline">Inspection Professionals</div>
    </div>
  </div>
  <div class="contact-panel">
    <h1 class="person-name">Dana Whitfield</h1>
    <p class="person-title">Certified Mold Inspector</p>
    <ul class="contact-list">
      <li>
        <svg viewBox="0 0 12 12" aria-hidden="true"><path d="M2.5 1 L4.5 1 L5.2 3.6 L4 4.6 Q5 7 7.4 8 L8.4 6.8 L11 7.5 L11 9.5 Q10.5 11 9 11 Q1 10 1 2.5 Q1 1 2.5 1Z" fill="#fff"/></svg>
        800.555.0142
      </li>
      <li>
        <svg viewBox="0 0 12 12" aria-hidden="true"><rect x="3" y="0.8" width="6" height="10.4" rx="1" fill="none" stroke="#fff" stroke-width="1.2"/><circle cx="6" cy="9.3" r="0.7" fill="#fff"/></svg>
        562.555.0193
      </li>
      <li>
        <svg viewBox="0 0 12 12" aria-hidden="true"><rect x="0.8" y="2.5" width="10.4" height="7" fill="none" stroke="#fff" stroke-width="1.2"/><path d="M1 3 L6 6.6 L11 3" fill="none" stroke="#fff" stroke-width="1.2"/></svg>
        dana@summitcrestinspect.com
      </li>
      <li>
        <svg viewBox="0 0 12 12" aria-hidden="true"><circle cx="6" cy="6" r="5" fill="none" stroke="#fff" stroke-width="1.2"/><ellipse cx="6" cy="6" rx="2.2" ry="5" fill="none" stroke="#fff" stroke-width="1"/><line x1="1" y1="6" x2="11" y2="6" stroke="#fff" stroke-width="1"/></svg>
        www.SummitCrestInspect.com
      </li>
    </ul>
  </div>
</section>

</body>
</html>
```